KTR Design Business Card

I need to develop a business card for my real estate design and investment company. Something clean, classic and professional with a modern vibe.

Industry/Entity Type

Real Estate

Font styles to use
Serif
Sans Serif

```html
<!DOCTYPE html>
<html lang="en">
<head>
<meta charset="utf-8">
<title>KTR Design Business Card</title>
<link rel="stylesheet" href="https://fonts.googleapis.com/css2?family=Exo+2:wght@300;400;600&display=swap">
<style>
  :root {
    --page: #e4e4e4;
    --card-white: #f7f7f7;
    --panel-dark: #353535;
    --band-grey: #a9a9ab;
    --ink-dark: #3a3a3a;
    --ink-light: #ffffff;
    --ink-muted: #d8d8d8;
  }
  * { margin: 0; padding: 0; box-sizing: border-box; }
  html, body {
    width: 1200px;
    height: 900px;
    overflow: hidden;
    background: var(--page);
    font-family: "Exo 2", sans-serif;
  }
  .card {
    position: absolute;
    left: 150px;
    top: 193px;
    width: 900px;
    height: 514px;
    border-radius: 44px;
    overflow: hidden;
    background: var(--card-white);
    box-shadow: 0 10px 30px rgba(0,0,0,0.15);
  }
  .card-shapes {
    position: absolute;
    inset: 0;
  }
  .brand {
    position: absolute;
    left: 90px;
    top: 220px;
    color: var(--ink-dark);
    font-weight: 300;
    font-size: 58px;
    letter-spacing: 1px;
  }
  .details {
    position: absolute;
    right: 56px;
    top: 46px;
    text-align: right;
    color: var(--ink-light);
  }
  .person-name {
    font-size: 28px;
    font-weight: 600;
    letter-spacing: 2px;
    text-transform: uppercase;
  }
  .person-role {
    font-size: 18px;
    color: var(--ink-muted);
    margin-top: 2px;
  }
  .address {
    font-size: 19px;
    line-height: 1.3;
    margin-top: 50px;
  }
  .contact-list {
    list-style: none;
    margin-top: 40px;
  }
  .contact-list li {
    font-size: 18px;
    line-height: 1;
    margin-bottom: 14px;
    display: flex;
    justify-content: flex-end;
    align-items: center;
    gap: 10px;
    letter-spacing: 1px;
  }
  .contact-list li.web-line { letter-spacing: 0.5px; }
  .contact-icon {
    width: 18px;
    height: 18px;
    flex: none;
    fill: none;
    stroke: var(--ink-light);
    stroke-width: 1.6;
  }
  .contact-list li.text-only { padding-right: 28px; }
</style>
</head>
<body>
  <div class="card">
    <svg class="card-shapes" viewBox="0 0 900 514" width="900" height="514" aria-hidden="true">
      <rect x="0" y="0" width="900" height="514" fill="var(--panel-dark)"/>
      <circle cx="128" cy="300" r="428" fill="var(--band-grey)"/>
      <circle cx="96" cy="300" r="424" fill="var(--card-white)"/>
    </svg>

    <div class="brand">KTR Design</div>

    <div class="details">
      <div class="person-name">Daniel Brooks</div>
      <div class="person-role">Managing Director</div>
      <div class="address">27 Harbour View, Level 9<br>Westgate Road</div>
      <ul class="contact-list">
        <li>021 555 0142
          <svg class="contact-icon" viewBox="0 0 24 24"><path d="M5 3h4l2 5-3 2a12 12 0 0 0 6 6l2-3 5 2v4a2 2 0 0 1-2 2A17 17 0 0 1 3 5a2 2 0 0 1 2-2z"/></svg>
        </li>
        <li>021 555 0143
          <svg class="contact-icon" viewBox="0 0 24 24"><rect x="7" y="2" width="10" height="20" rx="2"/><line x1="11" y1="18" x2="13" y2="18"/></svg>
        </li>
        <li>021 555 0144
          <svg class="contact-icon" viewBox="0 0 24 24"><rect x="4" y="9" width="16" height="11" rx="1"/><rect x="7" y="3" width="10" height="6"/><line x1="8" y1="13" x2="16" y2="13"/><line x1="8" y1="16" x2="16" y2="16"/></svg>
        </li>
        <li>hello@ktrdesign.com
          <svg class="contact-icon" viewBox="0 0 24 24"><rect x="3" y="5" width="18" height="14" rx="1"/><path d="M3 6l9 7 9-7"/></svg>
        </li>
        <li class="web-line">www.ktrdesign.com
          <svg class="contact-icon" viewBox="0 0 24 24"><circle cx="12" cy="12" r="9"/><ellipse cx="12" cy="12" rx="4" ry="9"/><line x1="3" y1="12" x2="21" y2="12"/></svg>
        </li>
      </ul>
    </div>
  </div>
</body>
</html>
```